Flyer, poster, banner and social media titles designs for Community Mending Chartre

The Harbourline Charter for Community Mending provide a nationally agreed framework to guide recovery policy and practice across Australia. The Principles support recovery practitioners, governments, non-government organisations and communities to deliver effective, community-centred recovery outcomes.
The Principles have recently been refreshed through extensive consultation and we require a contemporary visual identity and design suite that will increase awareness, engagement and practical application of the Principles.
The redesign will cover:
• A4 Brochure (primary publication)
• A3 Poster
• Pull up banner
• Social Media Tiles
The new design should:
• Create a recognisable brand for the Harbourline Charter.
• Appeal to both experienced and emerging recovery practitioners.
• Reflect contemporary disaster recovery practice.
• Feel people-focused rather than government-focused.
• Support future resources such as videos, implementation guides, presentations and workshop materials.
• Remain relevant for several years without requiring a major redesign.
Target Audience
• Disaster recovery practitioners
• Government agencies
• Non-government organisations
• Community recovery workers
• Recovery managers and leaders
• Community stakeholders and volunteers
The visual identity should reflect the six Principles:
• Understanding Context
• Recognising Complexity
• Community-Centred Approaches
• Coordination
• Communication
• Capacity Building
The design should communicate:
• Recovery is centred on people and communities.
• Recovery is collaborative and involves many sectors.
• Recovery is adaptive, inclusive and evidence-informed.
• Recovery supports resilience and long-term wellbeing.
• The Principles provide practical guidance for recovery practice.
We are looking for:
• Modern and professional
• Warm and approachable
• Human-centred
• Inclusive and accessible
• Australian in context
• Visually engaging
• Suitable for print and digital use
We would like to avoid:
• Images of disaster destruction
• Emergency response imagery (fire trucks, flashing lights, etc.)
• Overly corporate or bureaucratic designs
• Designs that focus on deficits rather than recovery and growth
Consider themes such as:
• Connection and collaboration
• Communities and people
• Growth, recovery and renewal
Accessibility
Designs should:
• Meet accessibility best practice
• Use clear typography
• Achieve strong colour contrast
• Be suitable for both digital and print formats

Deliverables
1. Principles Brochure
• A4 trifold size x 2 (online and print friendly version)
• A side to include cover side, logos side and overview of principles.
• B side full details of the principles
• Graphic to highlight the 3 c’s concept (RECOVERY Context, complexity, community centred, coordinate, communicate and capacity). Currently 3 circles.
• Can be printed and distributed electronically
2. Poster
• A1 and A3 versions
• Suitable for office and workshop display
3. Pull-Up Banner - 850 mm (W) × 2000 mm (H)
• Conference and event use
• High visual impact
• Strong branding and concise messaging
4. Social Media Tiles x 3

We are providing an extension and increasing the budget following feedback from designers. We are wanting the resources to look and feel different from the existing designs, considering either a different colour palette in the designs or different motif with the leave design. Any nature based designs should consider the Australian fauna or flora. Also suggest avoiding images in the designs. The principles are not numbered or liner in the concept of how they function. Happy to answer any further questions and thank you for your suggested concepts.

Disaster recovery practitioners, Government agencies , Non-government organisations, Community recovery workers and Community stakeholders and volunteers

Disaster recovery

• Modern, warm, visually engaging, human-centred, Australian in context and different to the current design.
• Symbols for each principles
• Images of disaster destruction, Emergency response imagery, Overly corporate or bureaucratic designs, Designs that focus on deficits rather than recovery and growth, avoid too much black

```html
<!DOCTYPE html>
<html lang="en">
<head>
<meta charset="utf-8">
<title>Harbourline Charter for Community Mending – Poster</title>
<link href="https://fonts.googleapis.com/css2?family=Poppins:wght@400;500&family=Tenor+Sans&family=Urbanist:wght@600&display=swap" rel="stylesheet">
<style>
  :root {
    --backdrop: #b5b5b5;
    --paper: #ffffff;
    --charcoal: #3d3d3d;
    --charcoal-soft: #474747;
    --green: #789b2d;
    --green-bright: #8cb43a;
    --ink: #2b2b2b;
    --white: #ffffff;
    --logo-blue: #3aa7d8;
  }
  * { box-sizing: border-box; margin: 0; padding: 0; }
  html, body { width: 1200px; height: 1187px; overflow: hidden; }
  body { background: var(--backdrop); font-family: "Poppins", sans-serif; position: relative; }

  .poster {
    position: absolute; left: 190px; top: 14px;
    width: 820px; height: 1159px;
    background: var(--paper); overflow: hidden;
  }
  .dark-band { position: absolute; left: 0; top: 258px; width: 100%; bottom: 0; background: var(--charcoal); }

  .title-kicker {
    position: absolute; left: 59px; top: 62px;
    font-size: 24px; letter-spacing: 1.6px; color: var(--ink); font-weight: 400;
  }
  .title-main {
    position: absolute; left: 56px; top: 92px;
    font-family: "Urbanist", sans-serif; font-weight: 600;
    font-size: 60px; letter-spacing: -1.5px; color: var(--charcoal); white-space: nowrap;
  }
  .title-main .accent { color: var(--green); }

  .leaf-art {
    position: absolute; left: 640px; top: 0; width: 130px; height: 166px;
    background: radial-gradient(ellipse at 60% 50%, #7ea72f 0%, rgba(126,167,47,0.55) 45%, rgba(255,255,255,0) 72%);
  }

  .intro-panel {
    position: absolute; left: 57px; top: 189px; width: 268px; height: 739px;
    background: var(--green); border-radius: 12px;
  }
  .intro-heading {
    position: absolute; left: 34px;
    font-family: "Tenor Sans", sans-serif; font-size: 25px; line-height: 30px; color: var(--ink);
  }
  .intro-text {
    position: absolute; left: 34px; width: 196px;
    font-size: 13px; line-height: 16.4px; color: var(--white);
  }

  .recovery-wheel { position: absolute; left: 84px; top: 817px; width: 214px; height: 214px; }
  .recovery-wheel text { font-family: "Poppins", sans-serif; }

  .partner-mark {
    position: absolute; left: 118px; top: 1050px;
    display: flex; align-items: center; gap: 10px;
  }
  .partner-mark .mark-square { width: 28px; height: 28px; background: var(--logo-blue); }
  .partner-mark .mark-name { font-size: 10px; line-height: 12px; color: var(--white); width: 110px; }

  .principles-box {
    position: absolute; left: 340px; top: 189px; width: 428px; height: 889px;
    border: 1.5px solid var(--white); border-radius: 12px;
  }
  .principles-box-top {
    position: absolute; left: 340px; top: 189px; width: 428px; height: 69px;
    border: 1.5px solid var(--green); border-bottom: none; border-radius: 12px 12px 0 0;
    background: var(--paper);
  }
  .principles-title {
    position: absolute; left: 340px; top: 207px; width: 428px; text-align: center;
    font-family: "Tenor Sans", sans-serif; font-size: 28px; color: var(--ink); letter-spacing: -0.3px;
  }

  .principle { position: absolute; left: 370px; width: 380px; }
  .principle-icon {
    position: absolute; left: 0; top: 2px; width: 36px; height: 36px; border-radius: 50%;
    background: var(--green);
  }
  .principle-icon svg { width: 36px; height: 36px; }
  .principle-name {
    margin-left: 44px;
    font-family: "Tenor Sans", sans-serif; font-size: 17px; line-height: 21px; color: var(--green-bright);
  }
  .principle-text {
    margin-left: 44px; margin-top: 4px; width: 316px;
    font-size: 13px; line-height: 16.4px; color: var(--white);
  }
</style>
</head>
<body>
<main class="poster">
  <div class="dark-band"></div>

  <p class="title-kicker">HARBOURLINE CHARTER FOR</p>
  <h1 class="title-main">Community <span class="accent">Mending</span></h1>
  <div class="leaf-art" role="img" aria-label="Illustration of a sprig of green eucalyptus leaves"></div>

  <section class="intro-panel">
    <h2 class="intro-heading" style="top:40px">DISASTER<br>RECOVERY</h2>
    <p class="intro-text" style="top:110px">Is part of emergency management, which includes the broader components of prevention, preparedness and response. Planning for recovery is integral to emergency preparation, and mitigation actions are often initiated as part of recovery.</p>
    <h2 class="intro-heading" style="top:326px">DISASTER<br>RECOVERY</h2>
    <p class="intro-text" style="top:396px">Includes built, environmental and economic elements, as well as individual and social wellbeing. Recovery can provide an opportunity to improve these aspects beyond previous conditions, by enhancing social and natural environments, infrastructure and economies –contributing to more resilient communities.</p>
  </section>

  <svg class="recovery-wheel" viewBox="0 0 200 200" role="img" aria-label="Recovery at the centre, surrounded by community-led, capacity, coordinate and communicate, framed by context and complexity">
    <defs>
      <path id="arc-top" d="M29,100 A71,71 0 0,1 171,100"/>
      <path id="arc-bottom" d="M21,100 A79,79 0 0,0 179,100"/>
      <path id="ring-mid" d="M51,100 A49,49 0 1,1 149,100 A49,49 0 1,1 51,100"/>
    </defs>
    <circle cx="100" cy="100" r="86" fill="var(--charcoal)"/>
    <circle cx="100" cy="100" r="64" fill="var(--charcoal-soft)"/>
    <circle cx="100" cy="100" r="39" fill="var(--green)"/>
    <text font-size="9.5" fill="#fff" letter-spacing="1"><textPath href="#arc-top" startOffset="50%" text-anchor="middle">CONTEXT</textPath></text>
    <text font-size="9.5" fill="#fff" letter-spacing="1.4"><textPath href="#arc-bottom" startOffset="50%" text-anchor="middle">COMPLEXITY</textPath></text>
    <text font-size="7" fill="var(--green-bright)"><textPath href="#ring-mid" textLength="300" lengthAdjust="spacing">COMMUNITY-LED • CAPACITY • COORDINATE • COMMUNICATE •</textPath></text>
    <text x="100" y="103.5" font-size="10" fill="#fff" text-anchor="middle" font-weight="500">RECOVERY</text>
  </svg>

  <div class="partner-mark">
    <span class="mark-square"></span>
    <span class="mark-name">Tidewell Recovery Circle</span>
  </div>

  <div class="principles-box"></div>
  <div class="principles-box-top"></div>
  <h2 class="principles-title">SUCCESSFUL RECOVERY</h2>

  <article class="principle" style="top:298px">
    <span class="principle-icon"><svg viewBox="0 0 36 36" fill="none" stroke="#fff" stroke-width="1.2"><rect x="12" y="10" width="12" height="16" rx="1"/><path d="M14.5 14h7M14.5 17h7M14.5 20h5"/></svg></span>
    <h3 class="principle-name">UNDERSTAND THE CONTEXT</h3>
    <p class="principle-text">Successful recovery is based on an understanding of the community context, with each community having its own history, values and dynamics.</p>
  </article>

  <article class="principle" style="top:422px">
    <span class="principle-icon"><svg viewBox="0 0 36 36" fill="none" stroke="#fff" stroke-width="1.2"><circle cx="18" cy="18" r="8"/><circle cx="18" cy="18" r="3"/><path d="M18 10v5M18 21v5M10 18h5M21 18h5M12.5 12.5l3.5 3.5M20 20l3.5 3.5M23.5 12.5L20 16M16 20l-3.5 3.5"/></svg></span>
    <h3 class="principle-name">RECOGNISE COMPLEXITY</h3>
    <p class="principle-text">Successful recovery is responsive to the complex and evolving nature of disasters and their impacts on communities, including compounding, cascading and concurrent events.</p>
  </article>

  <article class="principle" style="top:560px">
    <span class="principle-icon"><svg viewBox="0 0 36 36" fill="none" stroke="#fff" stroke-width="1.2"><path d="M14 20a6 6 0 1 1 8 0v3h-8z"/><path d="M15 26h6M18 8v-1.5M10 12l-1.2-1M26 12l1.2-1"/></svg></span>
    <h3 class="principle-name">USE COMMUNITY-CENTRED<br>APPROACHES</h3>
    <p class="principle-text">Successful recovery is community-centred, responsive and flexible, engaging with community and supporting them to move forward, with shared responsibilities.</p>
  </article>

  <article class="principle" style="top:709px">
    <span class="principle-icon"><svg viewBox="0 0 36 36" fill="none" stroke="#fff" stroke-width="1.2"><circle cx="12" cy="12" r="3"/><circle cx="24" cy="12" r="3"/><circle cx="12" cy="24" r="3"/><circle cx="24" cy="24" r="3"/><circle cx="18" cy="18" r="2"/><path d="M14 14l2.5 2.5M22 14l-2.5 2.5M14 22l2.5-2.5M22 22l-2.5-2.5"/></svg></span>
    <h3 class="principle-name">COORDINATE ALL ACTIVITIES</h3>
    <p class="principle-text">Successful recovery requires a planned, coordinated and adaptive approach, between community and partner agencies, based on continuing assessment of impacts and needs.</p>
  </article>

  <article class="principle" style="top:833px">
    <span class="principle-icon"><svg viewBox="0 0 36 36" fill="none" stroke="#fff" stroke-width="1.2"><circle cx="14" cy="13" r="2.5"/><path d="M10 27v-7a4 4 0 0 1 8 0v7M20 9h7v5h-4l-2 2v-2h-1z"/></svg></span>
    <h3 class="principle-name">COMMUNICATE EFFECTIVELY</h3>
    <p class="principle-text">Successful recovery is built on effective communication between the affected community and other partners.</p>
  </article>

  <article class="principle" style="top:948px">
    <span class="principle-icon"><svg viewBox="0 0 36 36" fill="none" stroke="#fff" stroke-width="1.2"><rect x="10" y="9" width="16" height="9" rx="1"/><circle cx="13" cy="23" r="2"/><circle cx="18" cy="23" r="2"/><circle cx="23" cy="23" r="2"/><path d="M10 28a3 3 0 0 1 6 0M15 28a3 3 0 0 1 6 0M20 28a3 3 0 0 1 6 0"/></svg></span>
    <h3 class="principle-name">RECOGNISE AND BUILD CAPACITY</h3>
    <p class="principle-text">Successful recovery recognises, supports and builds on individual, community and organisational capacity and resilience.</p>
  </article>
</main>
</body>
</html>
```